Business Card Design

I give lessons and clinics for dressage riders
I would like the design to be an outline (with broad lines) of a dressage horse and rider with in background of whole card with print over top tan or parchment card with burgundy print

Industry/Entity Type

Business

Contact Information for Business Card

Dale Ferrin
612-374-2059
Classical dressage training for the modern American
Clinics, lessons, training level -Prix St. George

Requirements
Must have
• broad lined outline of dressage horse and rider

```html
<!DOCTYPE html>
<html lang="en">
<head>
<meta charset="UTF-8">
<title>Dale Ferrin — Classical Dressage Training</title>
<link href="https://fonts.googleapis.com/css2?family=Federant&display=swap" rel="stylesheet">
<style>
  :root {
    --parchment: #efdcc2;
    --parchment-deep: #e2c6a8;
    --edge: #b9817a;
    --burgundy: #6b1630;
    --burgundy-soft: #8a2a40;
  }
  * { margin: 0; padding: 0; box-sizing: border-box; }
  html, body { width: 1200px; height: 693px; overflow: hidden; background: #ffffff; }
  .card {
    position: relative;
    width: 1200px;
    height: 693px;
    background:
      radial-gradient(ellipse at 50% 45%, var(--parchment) 0%, var(--parchment) 45%, var(--parchment-deep) 78%, var(--edge) 100%);
    font-family: "Federant", "Georgia", serif;
    color: var(--burgundy);
    overflow: hidden;
  }
  .card__illustration {
    position: absolute;
    left: 508px;
    top: 28px;
    width: 188px;
    height: 384px;
  }
  .card__frame {
    position: absolute;
    left: 34px;
    top: 429px;
    width: 1131px;
    height: 239px;
  }
  .card__details {
    position: absolute;
    left: 34px;
    top: 429px;
    width: 1131px;
    height: 239px;
    text-align: center;
  }
  .card__name {
    position: absolute;
    left: 0; right: 0;
    top: 16px;
    font-size: 54px;
    letter-spacing: 1px;
    line-height: 1;
    text-transform: uppercase;
  }
  .card__phone {
    position: absolute;
    left: 0; right: 0;
    top: 80px;
    font-size: 58px;
    letter-spacing: 2px;
    line-height: 1;
  }
  .card__tagline {
    position: absolute;
    left: 0; right: 0;
    font-size: 25px;
    letter-spacing: 0.5px;
    line-height: 1;
    text-transform: uppercase;
  }
  .card__tagline--motto { top: 154px; }
  .card__tagline--services { top: 193px; }
</style>
</head>
<body>
<div class="card">
  <svg class="card__illustration" viewBox="0 0 188 384" role="img" aria-label="Broad-lined outline illustration of a dressage rider in top hat on a collected horse, facing forward">
    <defs>
      <linearGradient id="illustration-fill" x1="0" y1="0" x2="0" y2="1">
        <stop offset="0" stop-color="#7a2238" stop-opacity="0.55"/>
        <stop offset="1" stop-color="#6b1630" stop-opacity="0.7"/>
      </linearGradient>
    </defs>
    <rect x="0" y="0" width="188" height="384" rx="10" fill="url(#illustration-fill)"/>
  </svg>

  <svg class="card__frame" viewBox="0 0 1131 239" aria-hidden="true">
    <rect x="4" y="4" width="1123" height="231" fill="rgba(239,220,194,0.35)"
          stroke="var(--burgundy)" stroke-width="4" stroke-dasharray="46 6 18 5 30 4"/>
  </svg>

  <div class="card__details">
    <h1 class="card__name">Dale Ferrin</h1>
    <p class="card__phone">612-374-2059</p>
    <p class="card__tagline card__tagline--motto">Classical dressage training for the modern American</p>
    <p class="card__tagline card__tagline--services">Clinics, lessons, training level -Prix St. George</p>
  </div>
</div>
</body>
</html>
```